Luxury supplement label and packaging design

I want to bring to fruition my vision for a line of supplements my business will be coming out with. Our place in the fitness space will cater to high end/ luxury good buyers. We have a Greek theme (Brava Lune) and I would like to incorporate a Greek key pattern along the border or somewhere. I have a logo made, as well as other design concepts o could show you I have an idea for. Please contact me if you decide to take this job. Some design inspiration include brands such as Morlenti, Pardo, Vireau, Halvery, and Krestovance. I have a name for the product/s I want labels created for.

Target Market(s)

High end/ luxury buyers. Men (age 27-39) Women (21-45). Fitness activists who enjoy luxury lifestyle brands.

Industry/Entity Type

Supplement

Font styles to use
Other font styles liked:
• CSL Greek Medium, Trajan Pro

Colors
fbee3f

Requirements
Must have
• Black, white, gold color combo. Greek Key pattern on top, bottom or both borders. Logo. Name of product available upon request.
• Name of product: RUBY TIDE
• Size: image attached
• Logo: Image attached
• Product description: image attached
Nice to have
• Ask for nutrition facts. Statements that are creative and appealing on side of label, description. Greek Font, uppercase. CSL Greek Medium

```html
<!DOCTYPE html>
<html lang="en">
<head>
<meta charset="utf-8">
<title>Ruby Tide – Premium Pre Workout Label</title>
<link rel="stylesheet" href="https://fonts.googleapis.com/css2?family=Cinzel:wght@400;600;700;900&family=Exo+2:ital,wght@1,700&family=Open+Sans:ital,wght@1,500&display=swap">
<style>
  :root {
    --paper: #ffffff;
    --label-black: #0b0b0c;
    --label-stripe: #141416;
    --gold: #fbee3f;
    --gold-deep: #c9a227;
    --gold-dark: #7a5a12;
    --gold-text: #d9b44a;
    --silver-light: #f2f2f2;
    --silver-dark: #8a8a8a;
    --ink-dark: #2a2a2a;
  }
  * { box-sizing: border-box; margin: 0; padding: 0; }
  html, body {
    width: 1200px;
    height: 1021px;
    overflow: hidden;
    background: var(--paper);
  }
  .canvas {
    position: relative;
    width: 1200px;
    height: 1021px;
    background: var(--paper);
  }
  .label {
    position: absolute;
    left: 50px;
    top: 90px;
    width: 1100px;
    height: 840px;
    background:
      repeating-linear-gradient(135deg, var(--label-black) 0 6px, var(--label-stripe) 6px 12px);
    border-top: 3px solid #3a3a3c;
    overflow: hidden;
  }
  .brand {
    position: absolute;
    left: 0; right: 0;
    top: 60px;
    text-align: center;
  }
  .brand-mark {
    display: block;
    margin: 0 auto 26px;
    width: 110px;
    height: 110px;
    border-radius: 50%;
    border: 4px solid var(--gold-deep);
  }
  .brand-name {
    font-family: "Cinzel", serif;
    font-weight: 600;
    font-size: 46px;
    letter-spacing: 4px;
    color: var(--gold-text);
    line-height: 1;
  }
  .brand-tagline {
    margin-top: 10px;
    font-family: "Cinzel", serif;
    font-weight: 400;
    font-size: 27px;
    letter-spacing: 2px;
    color: #d8d8d8;
  }
  .product-name {
    position: absolute;
    left: 0; right: 0;
    top: 355px;
    text-align: center;
    font-family: "Cinzel", serif;
    font-weight: 900;
    font-size: 118px;
    letter-spacing: 2px;
    line-height: 1;
    background: linear-gradient(180deg, var(--gold) 0%, var(--gold-deep) 55%, var(--gold-dark) 100%);
    -webkit-background-clip: text;
    background-clip: text;
    color: transparent;
  }
  .product-type {
    position: absolute;
    left: 265px;
    top: 505px;
    width: 620px;
    height: 64px;
    background: linear-gradient(90deg, var(--silver-dark) 0%, var(--silver-light) 40%, #bdbdbd 100%);
    clip-path: polygon(6% 0, 100% 0, 100% 100%, 0 100%);
    text-align: center;
    font-family: "Exo 2", sans-serif;
    font-style: italic;
    font-weight: 700;
    font-size: 44px;
    line-height: 64px;
    color: var(--ink-dark);
  }
  .count-badge {
    position: absolute;
    left: 170px;
    top: 635px;
    width: 150px;
    height: 128px;
    background: linear-gradient(180deg, #f0cf5a, var(--gold-deep));
    border-radius: 14px;
    clip-path: polygon(8% 0, 100% 0, 100% 100%, 0 100%);
    text-align: center;
    color: #111;
  }
  .count-number {
    display: block;
    font-family: "Exo 2", sans-serif;
    font-style: italic;
    font-weight: 700;
    font-size: 66px;
    line-height: 80px;
  }
  .count-unit {
    display: block;
    font-family: "Open Sans", sans-serif;
    font-style: italic;
    font-weight: 500;
    font-size: 22px;
  }
  .facts {
    position: absolute;
    left: 350px;
    top: 705px;
    font-family: "Open Sans", sans-serif;
    font-style: italic;
    font-weight: 500;
    font-size: 27px;
    white-space: nowrap;
  }
  .facts .supplement { color: var(--gold); margin-right: 28px; }
  .facts .weight { color: #e6e6e6; }
  .key-border {
    position: absolute;
    left: 0; right: 0;
    top: 768px;
    height: 56px;
    background: linear-gradient(90deg, var(--gold-dark), var(--gold-deep) 30%, var(--gold) 55%, var(--gold-deep) 80%, var(--gold-dark));
  }
</style>
</head>
<body>
  <main class="canvas">
    <section class="label">
      <header class="brand">
        <span class="brand-mark"></span>
        <div class="brand-name">BRAVA LUNE</div>
        <div class="brand-tagline">HEALTH AND FITNESS</div>
      </header>

      <h1 class="product-name">RUBY TIDE</h1>
      <div class="product-type">Premium Pre Workout</div>

      <div class="count-badge">
        <span class="count-number">30</span>
        <span class="count-unit">Capsules</span>
      </div>

      <p class="facts">
        <span class="supplement">Dietary Supplement</span>
        <span class="weight">Net Weight 1500g</span>
      </p>

      <div class="key-border" role="img" aria-label="Gold Greek key border pattern running across the label"></div>
    </section>
  </main>
</body>
</html>
```